business card

Business card for new business.
Red and black corporate colors.
Card can have an Indsutrial feel to it. Feel free to add Rust, Bolted steel, or graphics as you see fit. We provide highly specialized services to the below mentioned industries.
Keep information out of corners so that if I want I can choose rounded corners.
Information
- front. name - title - phone - email
- Rear
Welding - Piping - Fabrication - Rigging - Marine
Redwater - Harbourton - Pine Falls - Kestrel Bay - Northgate

```html
<!DOCTYPE html>
<html lang="en">
<head>
<meta charset="utf-8">
<title>Girderworks Business Card</title>
<link rel="stylesheet" href="https://fonts.googleapis.com/css2?family=Roboto:wght@400;500;900&display=swap">
<style>
  :root {
    --stage: #2b2b2b;
    --card-white: #ffffff;
    --steel: #7a7a7d;
    --steel-light: #8d8d90;
    --wave-grey: #88888b;
    --red: #e31b23;
    --ink: #555558;
    --white: #ffffff;
  }
  * { box-sizing: border-box; margin: 0; padding: 0; }
  html, body { width: 1200px; height: 930px; overflow: hidden; }
  body {
    background: var(--stage);
    font-family: "Roboto", Arial, sans-serif;
    position: relative;
  }
  .card {
    position: absolute;
    width: 600px;
    height: 340px;
    border-radius: 16px;
    overflow: hidden;
  }

  /* Rear side */
  .card-back {
    left: 80px; top: 90px;
    background: var(--steel);
  }
  .card-back .map-area {
    position: absolute;
    left: 90px; top: 40px;
    width: 430px; height: 230px;
    border-radius: 40% 50% 45% 40%;
    background: radial-gradient(ellipse at center, var(--steel-light) 0%, var(--steel) 72%);
  }
  .card-back .brand {
    position: absolute;
    left: 0; right: 0; top: 110px;
    text-align: center;
    color: var(--white);
    font-weight: 900;
    font-size: 50px;
    letter-spacing: 1px;
    text-transform: uppercase;
  }
  .card-back .lists {
    position: absolute;
    left: 0; right: 0; top: 230px;
    text-align: center;
    color: var(--white);
    font-size: 15px;
    line-height: 24px;
  }

  /* Front side */
  .card-front {
    left: 520px; top: 500px;
    background: var(--card-white);
  }
  .card-front .brand {
    position: absolute;
    left: 44px; top: 44px;
    display: flex; align-items: center; gap: 10px;
    color: var(--red);
    font-weight: 900;
    font-size: 40px;
    text-transform: uppercase;
    letter-spacing: 0.5px;
  }
  .card-front .brand .mark {
    width: 20px; height: 20px;
    background: var(--red);
  }
  .card-front .person {
    position: absolute;
    right: 40px; top: 60px;
    text-align: right;
  }
  .person .name {
    color: var(--red);
    font-weight: 500;
    font-size: 24px;
    text-transform: uppercase;
  }
  .person .title {
    color: var(--ink);
    font-size: 15px;
    margin-top: 2px;
  }
  .card-front .rule-top {
    position: absolute;
    right: 40px; top: 122px;
    width: 330px; height: 2px;
    background: var(--red);
  }
  .card-front .address {
    position: absolute;
    right: 40px; top: 134px;
    text-align: right;
    color: var(--ink);
    font-size: 15px;
    line-height: 21px;
  }
  .card-front .rule-bottom {
    position: absolute;
    left: 44px; top: 196px;
    width: 300px; height: 2px;
    background: var(--red);
  }
  .card-front .contacts {
    position: absolute;
    left: 44px; top: 208px;
    list-style: none;
    color: var(--ink);
    font-size: 16px;
    line-height: 25px;
  }
  .contacts li { display: flex; align-items: center; gap: 10px; }
  .contacts svg { width: 13px; height: 13px; }
  .contacts .accent { color: var(--red); }
  .card-front .wave {
    position: absolute;
    left: 0; bottom: 0;
    width: 600px; height: 340px;
  }
</style>
</head>
<body>

  <section class="card card-back" aria-label="Business card rear">
    <div class="map-area" role="img" aria-label="Faint dotted world map behind the company name"></div>
    <div class="brand">Girderworks</div>
    <div class="lists">
      <p class="industries">Welding - Piping - Fabrication - Rigging - Marine</p>
      <p class="cities">Redwater - Harbourton - Pine Falls - Kestrel Bay - Northgate</p>
    </div>
  </section>

  <section class="card card-front" aria-label="Business card front">
    <svg class="wave" viewBox="0 0 600 340" aria-hidden="true">
      <path d="M0 324 C210 324 340 305 440 250 C500 218 550 210 600 208 L600 340 L0 340 Z" fill="var(--wave-grey)"/>
      <path d="M0 314 C210 314 330 295 430 240 C490 208 545 200 600 198" fill="none" stroke="var(--red)" stroke-width="4"/>
      <path d="M0 320 C210 320 336 301 436 246 C496 214 548 206 600 204" fill="none" stroke="var(--white)" stroke-width="3"/>
    </svg>

    <div class="brand"><span class="mark"></span>Girderworks</div>

    <div class="person">
      <p class="name">Daniel Hart</p>
      <p class="title">Director</p>
    </div>
    <div class="rule-top"></div>
    <div class="address">
      <p>2290 Linden Ridge Rd.</p>
      <p>Millbrook, OR 97115</p>
    </div>

    <div class="rule-bottom"></div>
    <ul class="contacts">
      <li>
        <svg viewBox="0 0 24 24" aria-hidden="true"><path fill="var(--red)" d="M6.6 10.8a15 15 0 0 0 6.6 6.6l2.2-2.2c.3-.3.7-.4 1-.2 1.1.4 2.3.6 3.6.6.6 0 1 .4 1 1V20c0 .6-.4 1-1 1C10.6 21 3 13.4 3 4c0-.6.4-1 1-1h3.5c.6 0 1 .4 1 1 0 1.3.2 2.5.6 3.6.1.3 0 .7-.2 1z"/></svg>
        <span>+1 555-014-2273</span>
      </li>
      <li>
        <svg viewBox="0 0 24 24" aria-hidden="true"><rect x="3" y="5" width="18" height="14" rx="1" fill="none" stroke="var(--red)" stroke-width="2.5"/><path d="M3 6l9 7 9-7" fill="none" stroke="var(--red)" stroke-width="2.5"/></svg>
        <span>info@girderworks.com</span>
      </li>
      <li>
        <svg viewBox="0 0 24 24" aria-hidden="true"><circle cx="12" cy="12" r="9" fill="none" stroke="var(--red)" stroke-width="2.5"/><path d="M3 12h18M12 3c3 3 3 15 0 18M12 3c-3 3-3 15 0 18" fill="none" stroke="var(--red)" stroke-width="2"/></svg>
        <span>www.<span class="accent">girderworks</span>.com</span>
      </li>
    </ul>
  </section>

</body>
</html>
```